Law Firm Business Card

This is a business card for a law firm that serves US military and veterans.

The card must have ONLY the following (we want an uncluttered look):

- Company logo (PNG, GIF, JPEG copies uploaded)
- A tagline reading: "a law firm for service members and veterans"
- My name and title: "Tobias Marlow" and "Attorney"
- My email: "tobias.marlow@brinmoorlegal.com"
- My number: "855-FIRM-ONE (347-6663)"

We are looking for a clean, simple layout with only the above information, likely printed on a bright white cotton stock. The font of our logo is DIN 1451, and the font used on our website is Helvetica Neue. The color of our logo is #336699, and we probably want the tagline in that color also, and my contact information in a dark grey. Please review our website at www.brinmoorlegal.com to ensure your card design complements our website style.

Thanks and we look forward to seeing your submissions.

A few notes:

- Two-sided submissions are ok
- Please don't add graphics (scales of justice, judges hammer, etc)

```html
<!DOCTYPE html>
<html lang="en">
<head>
<meta charset="utf-8">
<title>Brinmoor Legal — Business Card</title>
<link rel="stylesheet" href="https://fonts.googleapis.com/css2?family=Crimson+Pro:ital,wght@0,400;1,600&display=swap">
<style>
  :root {
    --page-bg: #ece9e4;
    --card-front: #d3d3d3;
    --card-back: #2b68c9;
    --brand-blue: #2f67c6;
    --rule-blue: #3a6fc7;
    --star-blue: #5f86cf;
    --ink-grey: #4a4d55;
    --white: #ffffff;
  }
  * { margin: 0; padding: 0; box-sizing: border-box; }
  html, body {
    width: 1200px;
    height: 526px;
    overflow: hidden;
    background: var(--page-bg);
  }
  .stage {
    position: relative;
    width: 1200px;
    height: 526px;
  }
  .card {
    position: absolute;
    top: 98px;
    width: 520px;
    height: 330px;
    border-radius: 32px;
    overflow: hidden;
    text-align: center;
  }
  .card--front { left: 45px; background: var(--card-front); }
  .card--back { left: 635px; background: var(--card-back); }

  .edge-bar {
    position: absolute;
    width: 7px;
    height: 170px;
    background: var(--brand-blue);
  }
  .edge-bar--left { left: 0; top: 110px; }
  .edge-bar--right { right: 0; top: 40px; }

  .brand-name {
    position: absolute;
    left: 0;
    right: 0;
    display: flex;
    align-items: center;
    justify-content: center;
    gap: 14px;
    font-family: "Crimson Pro", Georgia, serif;
    font-weight: 400;
    line-height: 1;
  }
  .brand-name__mark { display: block; }
  .card--front .brand-name {
    top: 66px;
    font-size: 50px;
    color: var(--brand-blue);
  }
  .card--front .brand-name__mark {
    width: 18px; height: 18px;
    background: var(--brand-blue);
  }
  .card--back .brand-name {
    top: 104px;
    font-size: 62px;
    color: var(--white);
  }
  .card--back .brand-name__mark {
    width: 22px; height: 22px;
    background: var(--white);
  }

  .tagline {
    position: absolute;
    left: 0;
    right: 0;
    font-family: "Crimson Pro", Georgia, serif;
    font-weight: 400;
  }
  .card--front .tagline {
    top: 148px;
    font-size: 17px;
    color: var(--brand-blue);
  }
  .card--back .tagline {
    top: 206px;
    font-size: 20px;
    color: var(--white);
  }

  .holder {
    position: absolute;
    top: 178px;
    left: 0;
    right: 0;
    font-family: "Crimson Pro", Georgia, serif;
    color: var(--brand-blue);
  }
  .holder__name {
    font-style: italic;
    font-weight: 600;
    font-size: 22px;
  }
  .holder__title {
    font-size: 16px;
    color: var(--ink-grey);
  }
  .holder__rule-row {
    position: relative;
    width: 300px;
    height: 16px;
    margin: 2px auto 0;
  }
  .holder__rule {
    position: absolute;
    left: 20px;
    right: 20px;
    top: 7px;
    height: 1px;
    background: var(--rule-blue);
  }
  .holder__star {
    position: absolute;
    top: 0;
    width: 16px;
    height: 16px;
    fill: var(--star-blue);
  }
  .holder__star--left { left: 0; }
  .holder__star--right { right: 0; }

  .contact {
    position: absolute;
    top: 232px;
    left: 0;
    right: 0;
    list-style: none;
    font-family: "Crimson Pro", Georgia, serif;
    font-size: 16px;
    color: var(--ink-grey);
  }
  .contact__item {
    display: flex;
    align-items: center;
    justify-content: center;
    gap: 7px;
    margin-bottom: 4px;
  }
  .contact__icon { width: 13px; height: 13px; fill: var(--ink-grey); }
</style>
</head>
<body>
<main class="stage">
  <section class="card card--front" aria-label="Business card front">
    <span class="edge-bar edge-bar--left"></span>
    <span class="edge-bar edge-bar--right"></span>
    <div class="brand-name">
      <span class="brand-name__mark"></span>
      <span>Brinmoor Legal</span>
    </div>
    <p class="tagline">A Law Firm For Service Members And Veterans</p>
    <div class="holder">
      <span class="holder__name">Tobias Marlow,</span>
      <span class="holder__title">Attorney</span>
      <div class="holder__rule-row">
        <svg class="holder__star holder__star--left" viewBox="0 0 16 16" aria-hidden="true"><path d="M8 .8l2.1 4.9 5.2.5-4 3.5 1.2 5.2L8 12.2l-4.5 2.7 1.2-5.2-4-3.5 5.2-.5z"/></svg>
        <span class="holder__rule"></span>
        <svg class="holder__star holder__star--right" viewBox="0 0 16 16" aria-hidden="true"><path d="M8 .8l2.1 4.9 5.2.5-4 3.5 1.2 5.2L8 12.2l-4.5 2.7 1.2-5.2-4-3.5 5.2-.5z"/></svg>
      </div>
    </div>
    <ul class="contact">
      <li class="contact__item">
        <svg class="contact__icon" viewBox="0 0 16 16" aria-hidden="true"><path d="M3.6 1.2 6 3.6 4.8 5.6c.9 2 2.6 3.7 4.6 4.6l2-1.2 2.4 2.4-1.6 2.4C6.9 13.4 2.6 9.1 1.2 2.8z"/></svg>
        <span>855-FIRM-ONE (347-6663)</span>
      </li>
      <li class="contact__item">
        <svg class="contact__icon" viewBox="0 0 16 16" aria-hidden="true"><path d="M1 3h14v10H1zM2.2 4.2v.4L8 8.6l5.8-4v-.4zM2.2 6v5.8h11.6V6L8 10z"/></svg>
        <span>tobias.marlow@brinmoorlegal.com</span>
      </li>
    </ul>
  </section>

  <section class="card card--back" aria-label="Business card back">
    <div class="brand-name">
      <span class="brand-name__mark"></span>
      <span>Brinmoor Legal</span>
    </div>
    <p class="tagline">A Law Firm For Service Members &amp; Veterans</p>
  </section>
</main>
</body>
</html>
```